Brightmill Data Works

Our company is about IT hardwares and IT solutions. IT hardware such as PC, RAMS, storage and servers. IT solutions such as project management, BA. We are also selling new technology too.

Target Market(s)

Consumer, Small to Medium Business, Corporate

Requirements
Must have
• The business card must have the following:
• Name:
• Title:
• Contact Number:
• Email address:
• Website:
• Color: Must match the logo color upgrade

```html
<!DOCTYPE html>
<html lang="en">
<head>
<meta charset="utf-8">
<title>Brightmill Data Works – Business Card</title>
<link rel="stylesheet" href="https://fonts.googleapis.com/css2?family=Saira:wght@500;600;700&family=Saira+Semi+Condensed:wght@500&display=swap">
<style>
  :root {
    --bg: #dcdcdc;
    --card-white: #f7f7f5;
    --orange-light: #e3a24e;
    --orange: #d98a3c;
    --orange-deep: #c4672b;
    --charcoal: #4a4a4a;
    --slate: #565656;
    --white: #ffffff;
  }
  * { box-sizing: border-box; margin: 0; padding: 0; }
  html, body { width: 1200px; height: 864px; overflow: hidden; }
  body {
    background: var(--bg);
    font-family: "Saira", sans-serif;
    display: flex;
    align-items: center;
    justify-content: center;
    gap: 40px;
  }
  .card {
    position: relative;
    width: 560px;
    height: 320px;
    overflow: hidden;
    box-shadow: 0 10px 24px rgba(0,0,0,0.18);
  }

  /* Front */
  .card-front { background: linear-gradient(100deg, var(--orange-light) 0%, var(--orange) 55%, var(--orange-deep) 100%); }
  .front-panel { position: absolute; inset: 0; }
  .brand-name {
    position: absolute;
    left: 40px;
    top: 70px;
    width: 250px;
    font-weight: 700;
    font-size: 34px;
    line-height: 1.02;
    color: var(--charcoal);
    text-transform: uppercase;
    letter-spacing: 0.5px;
  }
  .brand-mark {
    position: absolute;
    left: 40px;
    top: 44px;
    width: 16px;
    height: 16px;
    background: var(--orange);
  }
  .person {
    position: absolute;
    right: 34px;
    top: 96px;
    text-align: right;
    font-family: "Saira Semi Condensed", sans-serif;
    font-weight: 500;
    text-transform: uppercase;
    line-height: 1.05;
  }
  .person-name { font-size: 20px; color: var(--charcoal); letter-spacing: 1px; }
  .person-title { font-size: 19px; color: var(--orange); letter-spacing: 1px; }
  .contacts {
    position: absolute;
    right: 34px;
    bottom: 30px;
    list-style: none;
    text-align: right;
    color: var(--white);
    font-size: 17px;
    letter-spacing: 1px;
    line-height: 1.55;
  }
  .contacts li { display: flex; align-items: center; justify-content: flex-end; gap: 10px; }
  .contact-icon { width: 18px; height: 18px; background: var(--white); display: inline-flex; align-items: center; justify-content: center; }
  .contact-icon svg { width: 13px; height: 13px; }

  /* Back */
  .card-back {
    background: radial-gradient(ellipse at 45% 40%, #5c5c5c 0%, var(--slate) 60%, #4b4b4b 100%);
    display: flex;
    align-items: center;
    justify-content: center;
    gap: 14px;
  }
  .back-mark { width: 18px; height: 18px; background: var(--orange); }
  .back-name {
    font-weight: 700;
    font-size: 38px;
    line-height: 1.02;
    color: var(--white);
    text-transform: uppercase;
    letter-spacing: 0.5px;
  }
</style>
</head>
<body>

  <article class="card card-front" aria-label="Business card front">
    <svg class="front-panel" viewBox="0 0 560 320" preserveAspectRatio="none" aria-hidden="true">
      <polygon points="0,22 560,22 560,172 310,172 275,196 0,196" fill="var(--card-white)"/>
    </svg>
    <span class="brand-mark" aria-hidden="true"></span>
    <div class="brand-name">Brightmill Data Works</div>

    <div class="person">
      <div class="person-name">Daniel Harrow</div>
      <div class="person-title">Manager</div>
    </div>

    <ul class="contacts">
      <li>+1-555-014-2870
        <span class="contact-icon"><svg viewBox="0 0 24 24"><path fill="var(--orange)" d="M6.6 10.8a15 15 0 0 0 6.6 6.6l2.2-2.2a1 1 0 0 1 1-.25 11.4 11.4 0 0 0 3.6.6 1 1 0 0 1 1 1V20a1 1 0 0 1-1 1A17 17 0 0 1 3 4a1 1 0 0 1 1-1h3.5a1 1 0 0 1 1 1c0 1.25.2 2.45.6 3.6a1 1 0 0 1-.25 1z"/></svg></span>
      </li>
      <li>daniel@brightmill.com
        <span class="contact-icon"><svg viewBox="0 0 24 24"><rect x="3" y="5" width="18" height="14" fill="none" stroke="var(--orange)" stroke-width="2"/><path d="M3 5l9 8 9-8M3 19l7-7M21 19l-7-7" fill="none" stroke="var(--orange)" stroke-width="2"/></svg></span>
      </li>
      <li>www.brightmill.com
        <span class="contact-icon"><svg viewBox="0 0 24 24"><circle cx="12" cy="12" r="9" fill="none" stroke="var(--orange)" stroke-width="2"/><path d="M3 12h18M12 3c3 3 3 15 0 18M12 3c-3 3-3 15 0 18" fill="none" stroke="var(--orange)" stroke-width="1.6"/></svg></span>
      </li>
    </ul>
  </article>

  <article class="card card-back" aria-label="Business card back">
    <span class="back-mark" aria-hidden="true"></span>
    <div class="back-name">Brightmill<br>Data Works</div>
  </article>

</body>
</html>
```